Awesome business card design needed

We need a new business card design to go with our new logo.
We are a web development agency that specialises in highly complex back-end integrations as opposed to design, our customers are retailers, hotels, hospitals and any other organisation that has a large online marketing department.
Take a look at our website - www.brenoloft.com for some inspiration.
We want our new business cards to exude class, professionalism and style.
We are likely to choose a high-end card to print them on but we want the design of the card itself to really turn heads.
We have no specific colour requirements, the logo as you will see is a turquoise colour R89 G171 B167 #59aba7 but it can also be in white if you want to make the colour of the card something different.
The information on the card should be:
Name
Position
Tel
email
Potentially a double sided card could have our web address, twitter and FB links.

```html
<!DOCTYPE html>
<html lang="en">
<head>
<meta charset="utf-8">
<title>Brenoloft Business Card</title>
<link href="https://fonts.googleapis.com/css2?family=Questrial&display=swap" rel="stylesheet">
<style>
  :root {
    --turquoise: #59aba7;
    --charcoal: #333335;
    --slate: #4a4a50;
    --white: #ffffff;
    --backdrop: #e9e8e5;
    --muted: #d8ecea;
  }
  * { box-sizing: border-box; margin: 0; padding: 0; }
  html, body {
    width: 1200px; height: 720px; overflow: hidden;
    background: var(--backdrop);
    font-family: "Questrial", "Century Gothic", sans-serif;
  }
  .canvas {
    width: 1200px; height: 720px;
    display: flex; align-items: center; justify-content: center; gap: 44px;
  }
  .card {
    width: 540px; height: 309px; position: relative; overflow: hidden;
    box-shadow: 0 6px 18px rgba(0,0,0,.18);
  }
  /* Front */
  .card-front { background: var(--white); }
  .front-logo {
    position: absolute; top: 58px; left: 0; right: 0; text-align: center;
    color: var(--turquoise); font-size: 68px; letter-spacing: 2px; line-height: 1;
  }
  .accent-strip {
    position: absolute; top: 164px; left: 0; width: 62%; height: 10px;
    background: var(--turquoise);
  }
  .name-band {
    position: absolute; top: 174px; left: 0; right: 0; height: 38px;
    background: var(--slate); color: var(--white);
    display: flex; align-items: center; padding-left: 150px;
    font-size: 17px; letter-spacing: .5px;
  }
  .name-band .name { font-weight: 700; }
  .name-band .position { font-size: 13px; margin-left: 6px; text-transform: uppercase; }
  .contact-band {
    position: absolute; top: 212px; left: 0; right: 0; bottom: 0;
    background: var(--turquoise); color: var(--white);
    display: flex; flex-direction: column; justify-content: center; gap: 12px;
    padding: 0 28px; font-size: 14px;
  }
  .contact-row { display: flex; align-items: center; gap: 22px; justify-content: center; }
  .contact-item { display: flex; align-items: center; gap: 7px; }
  .contact-item svg { width: 13px; height: 13px; fill: var(--white); }
  /* Back */
  .card-back { background: var(--charcoal); }
  .back-logo {
    position: absolute; top: 82px; left: 0; right: 0; text-align: center;
    color: var(--turquoise); font-size: 76px; letter-spacing: 2px; line-height: 1;
  }
  .follow {
    position: absolute; top: 194px; left: 0; right: 0;
    display: flex; align-items: center; justify-content: center; gap: 10px;
    color: var(--turquoise); font-size: 18px;
  }
  .social-square {
    width: 28px; height: 28px; border-radius: 5px; background: var(--muted);
  }
  .back-web {
    position: absolute; top: 240px; left: 0; right: 0; text-align: center;
    color: var(--white); font-size: 17px; letter-spacing: 3px;
  }
</style>
</head>
<body>
<main class="canvas">
  <section class="card card-front">
    <div class="front-logo">brenoloft</div>
    <div class="accent-strip"></div>
    <div class="name-band"><span class="name">YOUR NAME,</span><span class="position">Position</span></div>
    <div class="contact-band">
      <div class="contact-row">
        <span class="contact-item">
          <svg viewBox="0 0 16 16"><path d="M1 4h14v9H1z M1 4l7 5 7-5" fill="none" stroke="#fff" stroke-width="1.6"/></svg>
          info@brenoloft.com
        </span>
        <span class="contact-item">
          <svg viewBox="0 0 16 16"><circle cx="8" cy="8" r="6.5" fill="none" stroke="#fff" stroke-width="1.6"/><path d="M1.5 8h13M8 1.5c-3 3-3 10 0 13M8 1.5c3 3 3 10 0 13" fill="none" stroke="#fff" stroke-width="1.2"/></svg>
          www.brenoloft.com
        </span>
      </div>
      <div class="contact-row">
        <span class="contact-item">
          <svg viewBox="0 0 16 16"><path d="M4 1l3 3-2 2c1 2 3 4 5 5l2-2 3 3-2 3C7 15 1 9 1 3z"/></svg>
          123-456-7890
        </span>
        <span class="contact-item">Street Name, City Name, State Zip Code</span>
      </div>
    </div>
  </section>

  <section class="card card-back">
    <div class="back-logo">brenoloft</div>
    <div class="follow">
      <span>Follow Us On:</span>
      <span class="social-square" role="img" aria-label="Social network link"></span>
      <span class="social-square" role="img" aria-label="Social network link"></span>
    </div>
    <div class="back-web">www.brenoloft.com</div>
  </section>
</main>
</body>
</html>
```